Business Cards for new orthopaedic surgery practice

My husband and I are starting our own orthopaedic surgery practice. We are looking for a business card that is uniform, but one will have my name/title and the other will have his. You can just create one design with my name on it for now. But when I choose your design as the winning design I will ask that you add another copy with his name/title.

We are looking for classy, simple, elite all in one. We like dark blues/a little gold/yellow. Something that goes with our logo. We want our logo incorporated. Here is all the info you need:
Business name: RV Bone & Vitality Center
Location: 38517 North Willowmere Ave
Harlow Pines, FL 34870
Phone: 954-218-4063
Fax: 954-582-7341
Email: info@myrvbonecare.example

Names: Lydia Vance, M.D.
Board Certified Hand and Upper Extremity Surgeon

Ebo Dansu, M.D.
Board Certified Hip & Knee Replacement/General Orthopaedic Surgeon

Can decide what you want to put on the back. Maybe a slogan:
Steady in Care. Centered on You

I am just going to upload our logo. The only thing is if we select you as the winning design, the location, and phone numbers may change. We will need your help to update that once fully solidified.

Industry/Entity Type

Medical

Contact Information for Business Card

Colors
0054AA
0677BA
7BADD7
CADEEF
E8F1F8
0094D4
00A9DD
6FCCEA
C7EBF8
E9F6FB

Requirements
Must have
• class, appeal,
Should not have
• We want to air on the side of masculine if we are looking at masculine vs. feminine feel. But we still want it classy, sophisticated, and something we will love

```html
<!DOCTYPE html>
<html lang="en">
<head>
<meta charset="utf-8">
<title>RV Bone &amp; Vitality Center – Business Card</title>
<link rel="stylesheet" href="https://fonts.googleapis.com/css2?family=Montserrat:wght@400;500;700&display=swap">
<style>
  :root {
    --navy: #1b2a55;
    --pattern-a: #22347a;
    --pattern-b: #1a2a5e;
    --gold: #d6a54c;
    --white: #ffffff;
    --backdrop: #1e1f22;
  }
  * { box-sizing: border-box; margin: 0; padding: 0; }
  html, body { width: 1200px; height: 900px; overflow: hidden; }
  body {
    background: var(--backdrop);
    font-family: "Montserrat", Arial, sans-serif;
    display: flex; flex-direction: column; align-items: center; justify-content: center;
    gap: 24px;
  }
  .card {
    width: 700px; height: 400px; border-radius: 28px;
    background: var(--navy); position: relative; overflow: hidden;
  }
  /* Front */
  .brand {
    position: absolute; left: 40px; top: 0; width: 270px; height: 100%;
    display: flex; align-items: center; gap: 16px;
  }
  .brand-dot {
    flex: none; width: 22px; height: 22px; border-radius: 50%;
    border: 2px solid var(--gold);
  }
  .brand-name {
    color: var(--white); font-weight: 700; font-size: 27px; line-height: 1.22;
    letter-spacing: 0.04em; text-transform: uppercase;
  }
  .divider {
    position: absolute; left: 330px; top: 60px; width: 2px; height: 280px;
    background: var(--gold);
  }
  .details {
    position: absolute; left: 356px; top: 62px; right: 24px;
    color: var(--white); font-size: 14.5px; line-height: 1.35;
  }
  .doctor-name {
    color: var(--gold); font-weight: 700; font-size: 24px; letter-spacing: 0.02em;
    text-transform: uppercase; margin-bottom: 4px;
  }
  .doctor-title { margin-bottom: 10px; }
  .address { margin-bottom: 10px; }
  .contact-list { list-style: none; }
  .contact-list li { display: flex; align-items: center; gap: 8px; }
  .contact-list svg { width: 13px; height: 13px; flex: none; }
  .web-accent { color: var(--gold); }
  .slogan {
    color: var(--gold); font-weight: 500; font-size: 15px; margin-top: 14px;
    letter-spacing: 0.02em;
  }
  /* Back */
  .back-pattern {
    position: absolute; inset: 0;
    background: radial-gradient(circle at 50% 50%, var(--pattern-a), var(--pattern-b) 75%);
  }
  .back-brand {
    position: absolute; left: 50%; top: 50%; transform: translate(-50%, -50%);
    display: flex; align-items: center; gap: 10px; white-space: nowrap;
  }
  .back-brand .brand-dot { width: 14px; height: 14px; }
  .back-brand .brand-name { font-size: 14px; }
</style>
</head>
<body>
  <section class="card card-front">
    <div class="brand">
      <span class="brand-dot"></span>
      <p class="brand-name">RV Bone &amp;<br>Vitality<br>Center</p>
    </div>
    <div class="divider"></div>
    <div class="details">
      <h1 class="doctor-name">Lydia Vance, M.D</h1>
      <p class="doctor-title">Board Certified Hand and<br>Upper Extremity Surgeon</p>
      <p class="address">38517 North Willowmere Ave<br>Harlow Pines, FL 34870</p>
      <ul class="contact-list">
        <li><svg viewBox="0 0 16 16"><path d="M4 1.5l2.5 3-1.5 1.8c.9 1.8 2.3 3.2 4.1 4.1L11 9l3 2.5-1.6 2.6C7 14 2 9 1.9 3.6z" fill="var(--gold)"/></svg><span>954-218-4063</span></li>
        <li><svg viewBox="0 0 16 16"><rect x="2" y="6" width="12" height="7" rx="1" fill="none" stroke="var(--gold)" stroke-width="1.5"/><rect x="4.5" y="2" width="7" height="4" fill="none" stroke="var(--gold)" stroke-width="1.5"/></svg><span>954-582-7341</span></li>
        <li><svg viewBox="0 0 16 16"><rect x="1.5" y="3.5" width="13" height="9" fill="none" stroke="var(--gold)" stroke-width="1.4"/><path d="M1.5 3.5L8 9l6.5-5.5" fill="none" stroke="var(--gold)" stroke-width="1.4"/></svg><span>info@myrvbonecare.example</span></li>
        <li><svg viewBox="0 0 16 16"><circle cx="8" cy="8" r="6.3" fill="none" stroke="var(--gold)" stroke-width="1.4"/><path d="M1.7 8h12.6M8 1.7c-3 3.5-3 9 0 12.6M8 1.7c3 3.5 3 9 0 12.6" fill="none" stroke="var(--gold)" stroke-width="1.2"/></svg><span>www.<span class="web-accent">myrvbonecare</span>.example</span></li>
      </ul>
      <p class="slogan">Steady in Care. Centered on You</p>
    </div>
  </section>

  <section class="card card-back">
    <div class="back-pattern" role="img" aria-label="Subtle repeating brand emblem pattern in tonal blue"></div>
    <div class="back-brand">
      <span class="brand-dot"></span>
      <p class="brand-name">RV Bone &amp; Vitality Center</p>
    </div>
  </section>
</body>
</html>
```